Luxury Wine Label for New Startup Winery

We need a wine label for our new winery startup. We have worked with a local designer but do not feel the resulting label / logo have the elevation required to present our brand as a luxury wine. Our winery is called "Quailbrook Vineyards" and we are focused on extremely high quality hand crafted artisan and estate wines from the Pacific Northwest.
We would like to see designs that utilize a tree line, or other imagery that represents the "Quailbrook" part of our company name. Another interesting feature could be wood grain.
A logo will be required based on your design so please design with this in mind:
This logo should be consistent with the wine bottle label design, and should be representative of our high end exclusive wine while giving a sense of place (Oregon/ Pacific Northwest.)
I will supply an image of the design we received from our local designer, PLEASE NOTE: in general we do like wood grain and tree line concepts but feel the execution was poorly done.
ATTN: Logo design should be suitable for use on: Bottles (Red wine/rose/white wine), Bussiness cards, vehicle signage, business signage, etc
P.S.:
If you have a design that is not outside the box we are still interested in seeing it.
Label is for a burgundy style bottle with a label height of 3.5 - 4" and a width of 3.5-4"
any label <= 4"x4" and >=3.5"x3.5" will be acceptable:
HOWEVER Width should be greater than or equal to height due to the bottle format
Target Market(s)
Wine enthusiasts with adequate discretionary budgets to afford $100 bottles of wine.
Industry/Entity Type
Wine / Winery
Requirements
Must have
- A sense of luxury, a feel of exclusivity, and a theme consistent with our product and brand name
Nice to have
- Tree line, wood grain or other wood themes. Serif fonts
Should not have
- anything cheesy, off topic, hard to read script fonts or anything that makes the label hard to read from a few feet away or too busy

```html
<!DOCTYPE html>
<html lang="en">
<head>
<meta charset="utf-8">
<title>Quailbrook Vineyards – Pinot Noir Label</title>
<link rel="stylesheet" href="https://fonts.googleapis.com/css2?family=Josefin+Sans:wght@400&family=Michroma&display=swap">
<style>
  :root {
    --backdrop: #141414;
    --label-black: #0b0b0b;
    --band-dark: #1a1a1a;
    --band-mid: #2a2a2a;
    --gold: #e9a83a;
    --gold-light: #f7d36b;
    --gold-deep: #b8721c;
    --wood-light: #b8732a;
    --wood-dark: #5a2f10;
    --marble-dark: #121212;
    --marble-grey: #3a3a3a;
    --ink: #1a0f05;
  }
  * { margin: 0; padding: 0; box-sizing: border-box; }
  html, body {
    width: 1200px;
    height: 960px;
    overflow: hidden;
    background: var(--backdrop);
  }
  .canvas {
    position: relative;
    width: 1200px;
    height: 960px;
  }
  .wine-label {
    position: absolute;
    left: 120px;
    top: 60px;
    width: 960px;
    height: 840px;
    display: block;
    box-shadow: 0 20px 60px rgba(0,0,0,0.6);
  }
  .brand-name {
    font-family: "Josefin Sans", sans-serif;
    font-weight: 400;
    fill: var(--gold);
  }
  .varietal,
  .vintage,
  .volume {
    font-family: "Michroma", sans-serif;
  }
  .varietal { fill: var(--ink); }
  .vintage { fill: var(--ink); }
  .volume { fill: var(--gold); }
</style>
</head>
<body>
<main class="canvas">
  <svg class="wine-label" viewBox="0 0 1000 875" xmlns="http://www.w3.org/2000/svg" aria-label="Quailbrook Vineyards Pinot Noir 2025 wine label">
    <defs>
      <linearGradient id="band-fill" x1="0" y1="0" x2="1" y2="1">
        <stop offset="0" stop-color="var(--band-mid)"/>
        <stop offset="0.5" stop-color="var(--band-dark)"/>
        <stop offset="1" stop-color="var(--band-mid)"/>
      </linearGradient>
      <linearGradient id="marble-fill" x1="0" y1="0" x2="1" y2="1">
        <stop offset="0" stop-color="var(--marble-dark)"/>
        <stop offset="0.45" stop-color="var(--marble-grey)"/>
        <stop offset="0.6" stop-color="#6b4a1a"/>
        <stop offset="1" stop-color="var(--marble-dark)"/>
      </linearGradient>
      <linearGradient id="wood-fill" x1="0" y1="0" x2="0" y2="1">
        <stop offset="0" stop-color="var(--wood-light)"/>
        <stop offset="0.55" stop-color="#8e4f1b"/>
        <stop offset="1" stop-color="var(--wood-dark)"/>
      </linearGradient>
      <linearGradient id="gold-fill" x1="0" y1="0" x2="1" y2="0">
        <stop offset="0" stop-color="var(--gold-deep)"/>
        <stop offset="0.5" stop-color="var(--gold-light)"/>
        <stop offset="1" stop-color="var(--gold-deep)"/>
      </linearGradient>
      <clipPath id="diamond-clip">
        <polygon points="498,85 858,442 498,810 135,445"/>
      </clipPath>
    </defs>

    <!-- base and diagonal bands -->
    <rect class="label-base" width="1000" height="875" fill="url(#band-fill)"/>

    <!-- marble corners -->
    <polygon class="marble-corner" role="img" aria-label="Black marble texture with gold veins"
             points="0,0 580,0 0,580" fill="url(#marble-fill)"/>
    <polygon class="marble-corner" role="img" aria-label="Black marble texture with gold veins"
             points="1000,320 1000,875 445,875" fill="url(#marble-fill)"/>

    <!-- gold pinstripes -->
    <g class="pinstripes" stroke="var(--gold)" stroke-width="3" fill="none">
      <line x1="560" y1="0" x2="1000" y2="440"/>
      <line x1="650" y1="0" x2="1000" y2="350"/>
      <line x1="735" y1="0" x2="1000" y2="265"/>
      <line x1="0" y1="570" x2="305" y2="875"/>
      <line x1="60" y1="515" x2="420" y2="875"/>
      <line x1="0" y1="680" x2="195" y2="875"/>
    </g>

    <!-- diamond frame -->
    <polygon class="diamond-outline" points="498,62 881,442 498,833 112,445"
             fill="none" stroke="var(--gold)" stroke-width="3"/>

    <!-- diamond panel -->
    <g class="diamond-panel" clip-path="url(#diamond-clip)">
      <rect class="wood-panel" role="img" aria-label="Warm oak wood grain"
            x="100" y="80" width="800" height="740" fill="url(#wood-fill)"/>
      <polygon class="name-band" points="120,405 880,405 880,470 820,548 180,548 120,470" fill="var(--label-black)"/>
      <rect class="varietal-band" x="100" y="592" width="800" height="100" fill="url(#gold-fill)"/>
      <rect class="diamond-foot" x="100" y="692" width="800" height="130" fill="#3a1e0b"/>
    </g>

    <!-- brand -->
    <circle class="brand-mark" cx="498" cy="305" r="62" fill="none" stroke="var(--gold)" stroke-width="8"/>
    <text class="brand-name" x="498" y="475" text-anchor="middle" font-size="66" letter-spacing="4">QUAILBROOK</text>
    <text class="brand-name" x="498" y="528" text-anchor="middle" font-size="32" letter-spacing="6">VINEYARDS</text>

    <!-- varietal -->
    <text class="varietal" x="498" y="640" text-anchor="middle" font-size="30" letter-spacing="4">PINOT NOIR</text>
    <text class="vintage" x="498" y="672" text-anchor="middle" font-size="20" letter-spacing="3">-2025-</text>

    <!-- volume -->
    <text class="volume" x="48" y="835" font-size="38">25<tspan font-size="16" dy="-18" dx="6">OZ</tspan></text>
  </svg>
</main>
</body>
</html>
```